LM-Steuerberatung WordPress Site fully implemented (tax advisor)

Hello!
I need a little Wordpress Site for my newly founded Tax-Advisor Company.
I am a one-man Office advising in the area of Crypto-Currency.
PLEASE only provide a Design, if you can also Implement a WP-Site afterwards on an existing Webspace.

Please find the Content and Website-Description in the attached Document

Language for the Website is German (for now)

Target Market(s)

Tax-Advisory (specialized in Crypto Currency)

Coding

Coded - Design and coding required

Number of Pages Required

5+ page

Font styles to use
Sans Serif

Requirements
Must have
• Wordpress Implementation afterwards - Details according to attached Project Information Document

```html
<!DOCTYPE html>
<html lang="de">
<head>
<meta charset="utf-8">
<title>LM-Steuerberatung</title>
<link href="https://fonts.googleapis.com/css2?family=Roboto:wght@400;500;700&display=swap" rel="stylesheet">
<style>
  :root{
    --navy:#1b2a44;
    --navy-deep:#0a1a33;
    --text-dark:#1f2b40;
    --text-grey:#5b6270;
    --white:#ffffff;
    --line:#4a5870;
  }
  *{margin:0;padding:0;box-sizing:border-box}
  html,body{width:1200px;height:954px;overflow:hidden;font-family:"Roboto",Arial,sans-serif;background:var(--white)}
  .page{position:relative;width:1200px;height:954px}

  .site-header{position:absolute;top:0;left:0;width:1200px;height:117px;background:var(--white)}
  .brand{position:absolute;left:111px;top:62px;transform:translateY(-50%);display:flex;align-items:center;gap:12px;font-weight:700;font-size:22px;letter-spacing:.5px;color:var(--navy)}
  .brand-mark{width:40px;height:40px;background:var(--navy);border-radius:4px}
  .main-nav{position:absolute;top:62px;transform:translateY(-50%);left:565px;display:flex;gap:0;font-weight:500;font-size:15px;color:var(--text-grey)}
  .main-nav a{color:inherit;text-decoration:none;position:absolute;white-space:nowrap}
  .main-nav .active{color:var(--navy)}
  .social{position:absolute;top:45px;left:973px;display:flex;gap:7px}
  .social span{width:34px;height:34px;border-radius:50%;background:var(--white);box-shadow:0 2px 8px rgba(0,0,0,.15)}
  .social span.on{background:var(--navy)}

  .hero{position:absolute;top:117px;left:0;width:1200px;height:600px;color:var(--white);text-align:center}
  .hero-image{position:absolute;inset:0;background:
      radial-gradient(circle at 45% 80%,rgba(220,150,80,.35),transparent 12%),
      radial-gradient(ellipse at 90% 55%,#2d6fb3 0%,transparent 40%),
      linear-gradient(180deg,#063a7a 0%,#06244d 45%,#0a1a33 100%)}
  .hero-content{position:absolute;left:0;right:0;top:0}
  .hero-welcome{position:absolute;top:120px;width:100%;font-size:18px}
  .hero-title{position:absolute;top:160px;width:100%;font-size:20px;font-weight:700;line-height:31px;text-transform:uppercase}
  .hero-divider{position:absolute;top:231px;left:557px;width:86px;height:2px;background:var(--white)}
  .hero-text{position:absolute;top:253px;width:100%;font-size:16px;line-height:27px}
  .hero-button{position:absolute;top:328px;left:480px;width:240px;height:50px;background:var(--white);color:var(--navy);border-radius:3px;font-size:11.5px;font-weight:700;line-height:50px;text-decoration:none}
  .slider-dots{position:absolute;top:556px;left:575px;display:flex;gap:9px}
  .slider-dots span{width:11px;height:11px;border:1.5px solid var(--white);border-radius:50%}
  .slider-dots span.on{background:var(--white)}

  .site-footer{position:absolute;top:717px;left:0;width:1200px;height:237px;background:var(--navy);color:var(--white)}
  .footer-brand{position:absolute;left:111px;top:96px;transform:translateY(-50%);display:flex;align-items:center;gap:16px;font-weight:700;font-size:26px;letter-spacing:.5px}
  .footer-brand .brand-mark{width:50px;height:50px;background:var(--white)}
  .footer-nav{position:absolute;right:111px;top:80px;display:flex;gap:22px;font-weight:700;font-size:15.5px}
  .footer-contact{position:absolute;right:111px;top:117px;display:flex;align-items:center;gap:10px;font-size:14px}
  .footer-contact svg{fill:var(--white)}
  .footer-rule{position:absolute;left:111px;top:168px;width:978px;height:1px;background:var(--line)}
  .copyright{position:absolute;top:187px;width:100%;text-align:center;font-size:14.5px}
</style>
</head>
<body>
<div class="page">
  <header class="site-header">
    <div class="brand"><span class="brand-mark"></span>LM STEUERBERATUNG</div>
    <nav class="main-nav">
      <a class="active" style="left:0">HOME</a>
      <a style="left:63px">LEISTUNGEN&nbsp;&#8964;</a>
      <a style="left:195px">ÜBER MIC</a>
      <a style="left:291px">KONTAKT</a>
    </nav>
    <div class="social"><span class="on"></span><span></span><span></span></div>
  </header>

  <section class="hero">
    <div class="hero-image" role="img" aria-label="Foto: Hand mit leuchtendem Symbol vor blauem Netzwerk-Hintergrund"></div>
    <div class="hero-content">
      <p class="hero-welcome">Willkommen bei LM-Steuerberatung!</p>
      <h1 class="hero-title">Dann lass ich meine Kryptos auf einer Börse in<br>Singapur, dort ist das steuerfrei</h1>
      <div class="hero-divider"></div>
      <p class="hero-text">Ihrem Spezialisten bei allen steuerlichen Themen rund um Einkünfte<br>&amp; Vermögen aus Krypto-Assets.</p>
      <a class="hero-button">WEITER ZU UNSEREN LEISTUNGEN</a>
    </div>
    <div class="slider-dots"><span></span><span></span><span class="on"></span></div>
  </section>

  <footer class="site-footer">
    <div class="footer-brand"><span class="brand-mark"></span>LM STEUERBERATUNG</div>
    <nav class="footer-nav"><span>HOME</span><span>LEISTUNGEN</span><span>ÜBER MIC</span><span>&nbsp;KONTAKT</span></nav>
    <div class="footer-contact">
      <svg width="12" height="12" viewBox="0 0 24 24"><path d="M6.6 10.8a15.1 15.1 0 006.6 6.6l2.2-2.2c.3-.3.7-.4 1-.2 1.1.4 2.3.6 3.6.6.6 0 1 .4 1 1V20c0 .6-.4 1-1 1A17 17 0 013 4c0-.6.4-1 1-1h3.5c.6 0 1 .4 1 1 0 1.3.2 2.5.6 3.6.1.3 0 .7-.2 1z"/></svg>
      <span>+43 512 480 276</span><span>&nbsp;I&nbsp;</span>
      <svg width="14" height="11" viewBox="0 0 24 18"><path d="M0 0h24v2L12 10 0 2z M0 4l12 8 12-8v14H0z"/></svg>
      <span>office@lm-steuer.at</span>
    </div>
    <div class="footer-rule"></div>
    <p class="copyright">© 2022 LM-Steuerberatung &nbsp; | &nbsp; Impressum</p>
  </footer>
</div>
</body>
</html>
```